Business Card for a Jewellery Brand

Business card for an upscale jewellery brand. Attached is the brand logo and icon and color board. I am looking for two card versions: one for the founder and one is generic. The card should be elegant and convey upscale and premium feel. I am open to both square and rectangle card shapes.

Industry/Entity Type

Jewelry

Contact Information for Business Card

Two cards: (1) Sunela Parvaniya (Founder) (2) General
(1) Sunela Parvaniya card should have Name: Sunela Parvaniya, Title: Founder Email id: sunela@quiremo.com.au. Phone no: +61452913307
(2) Generic card should have Email id: info@quiremo.com.au. Phone no: +61436207518

Requirements
Must have
• Workmark
• ICON
• Phone no
• Email ID
• ABN: 58219740312 (Note: ABN is Business number in Australia)
• Website: www.quiremo.com.au
• Instagram: quiremo_jewellery
• Facebook: @quiremojewellery
Nice to have
• Tagline

```html
<!DOCTYPE html>
<html lang="en">
<head>
<meta charset="utf-8">
<title>Quiremo Business Cards</title>
<link rel="stylesheet" href="https://fonts.googleapis.com/css2?family=Barlow+Condensed:wght@600&family=Roboto:wght@400;500&display=swap">
<style>
  :root {
    --backdrop: #2a2a2a;
    --marble-light: #f6f6f7;
    --marble-mid: #e4e5e8;
    --marble-vein: #d3d5da;
    --rose: #e0979a;
    --rose-card: #cf8187;
    --blush: #fde7df;
    --blush-soft: #fbe3dd;
  }
  * { box-sizing: border-box; margin: 0; padding: 0; }
  html, body {
    width: 1200px;
    height: 960px;
    overflow: hidden;
    background: var(--backdrop);
  }
  .canvas {
    position: relative;
    width: 1200px;
    height: 960px;
  }
  .card {
    position: absolute;
    width: 600px;
    height: 342px;
  }

  /* Front card */
  .card--front {
    left: 302px;
    top: 129px;
  }
  .card__marble {
    position: absolute;
    inset: 0;
    background:
      linear-gradient(150deg, var(--marble-light) 0%, var(--marble-mid) 35%, var(--marble-light) 55%, var(--marble-vein) 78%, var(--marble-light) 100%);
  }
  .card--front .card__frame {
    position: absolute;
    left: 11px;
    top: 11px;
    right: 11px;
    bottom: 11px;
    border: 2px solid var(--rose);
  }
  .wordmark {
    position: absolute;
    left: 0;
    right: 0;
    top: 128px;
    text-align: center;
    font-family: "Roboto", sans-serif;
    font-weight: 500;
    font-size: 64px;
    line-height: 1;
    letter-spacing: 0.22em;
    padding-left: 0.22em;
    color: var(--rose);
  }

  /* Back card */
  .card--back {
    left: 299px;
    top: 488px;
    background: var(--rose-card);
  }
  .card--back .card__frame {
    position: absolute;
    left: 11px;
    top: 10px;
    right: 11px;
    bottom: 10px;
    border: 2px solid var(--blush);
  }
  .card__content {
    position: absolute;
    left: 0;
    right: 0;
    top: 82px;
    text-align: center;
    color: var(--blush-soft);
    font-family: "Roboto", sans-serif;
  }
  .brand-name {
    font-family: "Roboto", sans-serif;
    font-weight: 500;
    font-size: 22px;
    letter-spacing: 0.22em;
    padding-left: 0.22em;
    line-height: 1;
    color: var(--blush);
    margin-bottom: 52px;
  }
  .person-name {
    font-family: "Barlow Condensed", sans-serif;
    font-weight: 600;
    font-size: 24px;
    letter-spacing: 0.03em;
    line-height: 1;
    text-transform: uppercase;
    color: var(--blush);
  }
  .person-role {
    font-size: 15px;
    line-height: 1;
    margin-top: 6px;
  }
  .contact-list {
    list-style: none;
    margin-top: 12px;
    font-size: 14px;
    line-height: 19px;
  }
  .contact-row span {
    display: inline-flex;
    align-items: center;
    gap: 3px;
    margin: 0 2px;
  }
  .contact-icon {
    width: 12px;
    height: 12px;
    fill: var(--blush);
  }
  .social-mark {
    display: inline-block;
    width: 10px;
    height: 10px;
    background: var(--blush);
    border-radius: 1px;
  }
  .business-number {
    font-size: 14px;
    margin-top: 12px;
    line-height: 1;
  }
</style>
</head>
<body>
<main class="canvas">

  <section class="card card--front" aria-label="Card front">
    <div class="card__marble" role="img" aria-label="White marble texture background"></div>
    <div class="card__frame"></div>
    <div class="wordmark">QUIREMO</div>
  </section>

  <section class="card card--back" aria-label="Card back">
    <div class="card__frame"></div>
    <div class="card__content">
      <div class="brand-name">QUIREMO</div>
      <h1 class="person-name">Sunela Parvaniya</h1>
      <p class="person-role">Founder</p>
      <ul class="contact-list">
        <li class="contact-row">
          <span>
            <svg class="contact-icon" viewBox="0 0 12 12" aria-hidden="true"><path d="M3 0h6a1 1 0 0 1 1 1v10a1 1 0 0 1-1 1H3a1 1 0 0 1-1-1V1a1 1 0 0 1 1-1zm0 1.5v8h6v-8zM6 10a.6.6 0 1 0 0 1.2A.6.6 0 0 0 6 10z"/></svg>
            +61452913307
          </span>
          <span>
            <svg class="contact-icon" viewBox="0 0 12 12" aria-hidden="true"><path d="M0 2h12v1L6 7 0 3zM0 4.3l6 4 6-4V10H0z"/></svg>
            sunela@quiremo.com.au
          </span>
        </li>
        <li class="contact-row">
          <span>
            <svg class="contact-icon" viewBox="0 0 12 12" aria-hidden="true"><circle cx="6" cy="6" r="5.5"/><path d="M3 3.5c1 .3 1.5 1 1.3 2s.8 1.5 1.5 1.3M7.5 1.2c-.3 1 .3 1.8 1.3 1.8s1.6.8 1.5 1.8" stroke="#cf8187" stroke-width="1" fill="none"/></svg>
            quiremo.com.au
          </span>
          <span>
            <i class="social-mark" aria-hidden="true"></i>
            quiremo_jewellery
          </span>
          <span>
            <i class="social-mark" aria-hidden="true"></i>
            @quiremojewellery
          </span>
        </li>
      </ul>
      <p class="business-number">ABN:58219740312</p>
    </div>
  </section>

</main>
</body>
</html>
```